product development company BRVEMKO LLC business card

We need a business card design for a company based in Texas called 'BRVEMKO LLC'. Our first product is a illuminated portable ice chest that is called ' Copper Harbor coolers'. Copper harbor coolers is trademarked. I would like to have the copper harbor trademark somewhere on the card as well as the BRVEMKO LLC name.

Target Market(s)

outdoor industry

Industry/Entity Type

Business

Contact Information for Business Card

i would like to have BRVEMKO LLC logo larger than the Copper harbor coolers logo.

Font styles to use
Serif
Sans Serif

```html
<!DOCTYPE html>
<html lang="en">
<head>
<meta charset="utf-8">
<title>BRVEMKO LLC – Business Card</title>
<link rel="stylesheet" href="https://fonts.googleapis.com/css2?family=Tinos:wght@400;700&family=Source+Sans+3:wght@400;600&display=swap">
<style>
  :root {
    --brand-blue: #0a6cb8;
    --brand-green: #8fbf3a;
    --card-white: #ffffff;
    --ink: #111111;
    --backdrop: #e9e7e3;
  }
  * { margin: 0; padding: 0; box-sizing: border-box; }
  html, body { width: 1200px; height: 902px; overflow: hidden; }
  body { background: var(--backdrop); position: relative; }

  .card {
    position: absolute; left: 80px; top: 155px;
    width: 1040px; height: 592px;
    background: var(--card-white);
    border-radius: 22px; overflow: hidden;
    box-shadow: 0 6px 24px rgba(0,0,0,.12);
  }
  .card__wave { position: absolute; inset: 0; width: 100%; height: 100%; }

  .brand { position: absolute; left: 0; top: 0; width: 512px; }
  .brand__mark {
    position: absolute; left: 177px; top: 105px;
    width: 169px; height: 169px;
    background: var(--brand-blue);
  }
  .brand__name {
    position: absolute; left: 0; top: 300px; width: 512px;
    text-align: center;
    font-family: "Tinos", serif; font-weight: 400;
    font-size: 70px; letter-spacing: 1px; line-height: 1;
    color: var(--brand-blue);
  }
  .brand__suffix {
    position: absolute; left: 53px; top: 384px; width: 418px;
    display: flex; align-items: center; gap: 22px;
    font-family: "Tinos", serif; font-size: 46px; line-height: 1;
    color: var(--brand-blue);
  }
  .brand__suffix::before, .brand__suffix::after {
    content: ""; flex: 1; height: 2px; background: var(--brand-green);
  }

  .divider {
    position: absolute; left: 511px; top: 107px;
    width: 2px; height: 322px; background: var(--brand-green);
  }

  .contact { position: absolute; left: 559px; top: 0; }
  .contact__name {
    position: absolute; left: 0; top: 104px; white-space: nowrap;
    font-family: "Tinos", serif; font-size: 44px; line-height: 1;
    color: var(--brand-blue);
  }
  .contact__role {
    position: absolute; left: 0; top: 144px; white-space: nowrap;
    font-family: "Tinos", serif; font-weight: 700; font-size: 29px; line-height: 1;
    color: var(--brand-green);
  }
  .contact__line {
    position: absolute; left: 0; display: flex; align-items: center; gap: 11px;
    white-space: nowrap;
    font-family: "Source Sans 3", sans-serif; font-size: 29px; line-height: 1;
    color: var(--brand-blue);
  }
  .contact__line--phone { top: 239px; }
  .contact__line--email { top: 278px; }
  .contact__icon { width: 33px; height: 32px; flex: none; }
  .contact__web {
    position: absolute; left: 0; top: 325px; white-space: nowrap;
    font-family: "Tinos", serif; font-size: 27px; line-height: 1;
    color: var(--brand-green);
  }
  .product-name {
    position: absolute; left: 0; top: 382px; white-space: nowrap;
    font-family: "Tinos", serif; font-weight: 700; font-size: 34px; line-height: 1;
    color: var(--ink);
  }
</style>
</head>
<body>
  <div class="card">
    <svg class="card__wave" viewBox="0 0 940 535" preserveAspectRatio="none" aria-hidden="true">
      <path fill="var(--brand-blue)" d="M0 425 C150 472 300 512 450 508 C650 500 800 425 940 420 V535 H0 Z"/>
      <path fill="var(--brand-green)" d="M0 414 C150 458 300 494 430 492 C620 489 800 410 925 404 L930 412 C800 424 640 500 440 502 C300 505 150 470 0 420 Z"/>
    </svg>

    <div class="brand">
      <div class="brand__mark"></div>
      <div class="brand__name">BRVEMKO</div>
      <div class="brand__suffix">LLC</div>
    </div>

    <div class="divider"></div>

    <div class="contact">
      <div class="contact__name">EMPLOYEE NAME</div>
      <div class="contact__role">Maneger</div>

      <div class="contact__line contact__line--phone">
        <svg class="contact__icon" viewBox="0 0 32 32" aria-hidden="true">
          <rect width="32" height="32" rx="4" fill="var(--brand-green)"/>
          <path fill="#fff" d="M11 7c1 0 3 4 3 5s-2 1.5-2 2.5c0 2 3.5 5.5 5.5 5.5 1 0 1.5-2 2.5-2s5 2 5 3-2 4-4 4C14 25 7 18 7 11c0-2 3-4 4-4z"/>
        </svg>
        <span>123 456 7890</span>
      </div>
      <div class="contact__line contact__line--email">
        <svg class="contact__icon" viewBox="0 0 32 32" aria-hidden="true">
          <rect width="32" height="32" rx="4" fill="var(--brand-green)"/>
          <rect x="6" y="9" width="20" height="14" fill="none" stroke="#fff" stroke-width="2"/>
          <path d="M6 9 L16 17 L26 9" fill="none" stroke="#fff" stroke-width="2"/>
        </svg>
        <span>your@yourcompany.com</span>
      </div>
      <div class="contact__web">www.yourcompany.com</div>
      <div class="product-name">Copper Harbor</div>
    </div>
  </div>
</body>
</html>
```